Business card for marketing analytics company

Need a business card for new company. I have a logo already that I want to be built into the card and should use those colours

Company is called steered by tallies
Design must bring steered by tallies to life not be a card that could be for anyone with a logo put on it.

Like the front to be fairly clean and uncluttered bringing the logo out with a suitable design on the back of the card.

The logo represents a compass and business growth so those themes along with numbers, analytics , data are appropriate.
I'm often working with creative industries so also needs to reflect the creative side of analytics rather than be very corporate looking.

Target Market(s)

Ad agency, media agency, consumer goods clients

Industry/Entity Type

Market Research

Contact Information for Business Card

Needs to include name, title, email and phone number

Colors
f78f20
f68d4d
ec1f27

Requirements
Must have
• Must bring steered by tallies to life not be a card that could be for anyone with a logo put on it.
• Logo, Correct colours
• Like a design on the back that relates to company name
• Designs for both sides
Should not have
• Please do not just submit logo and a coloured card.
• It needs to have a design element to it
• No black background
• No clear cards - needs front & back

```html
<!DOCTYPE html>
<html lang="en">
<head>
<meta charset="utf-8">
<title>steered by tallies — business card</title>
<link rel="stylesheet" href="https://fonts.googleapis.com/css2?family=Montserrat:wght@500;600&family=Ubuntu:wght@400;700&display=swap">
<style>
  :root {
    --stage: #1c1c1d;
    --card: #333335;
    --ink-white: #ffffff;
    --ghost: #403f43;
    --ghost-soft: #3a3a3d;
    --brand-orange: #f78f20;
    --brand-peach: #f68d4d;
    --brand-red: #ec1f27;
  }
  * { box-sizing: border-box; margin: 0; padding: 0; }
  html, body {
    width: 1200px; height: 1000px; overflow: hidden;
    background: var(--stage);
  }
  .stage { position: relative; width: 1200px; height: 1000px; }

  .card {
    position: absolute;
    width: 580px; height: 330px;
    border-radius: 26px;
    background: var(--card);
    box-shadow: 0 18px 40px rgba(0,0,0,.45);
    overflow: hidden;
  }
  .card--back { left: 110px; top: 120px; }
  .card--front { left: 510px; top: 540px; }

  /* back side: faint tally groups rising into a growth chart */
  .back__tallies {
    position: absolute; right: 30px; top: 26px;
    width: 330px; height: 230px;
  }
  .back__brand {
    position: absolute; left: 34px; bottom: 34px;
    display: flex; align-items: center; gap: 12px;
  }
  .back__dot {
    width: 34px; height: 34px; border-radius: 50%;
    border: 3px solid var(--brand-orange);
  }
  .back__name {
    font-family: "Montserrat", sans-serif;
    font-weight: 600; font-size: 20px; line-height: 1;
    color: var(--brand-orange);
  }

  /* front side */
  .front__name {
    position: absolute; left: 34px; top: 96px;
    font-family: "Montserrat", sans-serif;
    font-weight: 600; font-size: 40px; line-height: 1.02;
    color: var(--ink-white);
  }
  .front__chart {
    position: absolute; right: 36px; top: 30px;
    width: 230px; height: 220px;
  }
  .person {
    position: absolute; left: 34px; top: 212px;
    font-family: "Ubuntu", sans-serif;
  }
  .person__name {
    font-weight: 700; font-size: 19px; letter-spacing: .5px;
    color: var(--brand-red); text-transform: uppercase;
  }
  .person__role {
    font-size: 13px; color: var(--ink-white); margin-top: 2px;
  }
  .contacts {
    list-style: none; margin-top: 8px;
    font-size: 11.5px; color: var(--ink-white);
  }
  .contacts li { display: flex; align-items: center; gap: 10px; line-height: 17px; }
  .contacts svg { width: 10px; height: 10px; fill: var(--brand-red); flex: none; }
  .contacts .accent { color: var(--brand-red); }
</style>
</head>
<body>
<main class="stage">

  <section class="card card--back" aria-label="Card back">
    <svg class="back__tallies" viewBox="0 0 330 230" aria-hidden="true"
         fill="none" stroke="var(--ghost)" stroke-width="7" stroke-linecap="round">
      <!-- tally group 1 -->
      <path d="M20 210 V170 M34 210 V170 M48 210 V170 M62 210 V170 M12 200 L70 178"/>
      <!-- tally group 2 -->
      <path d="M100 210 V140 M114 210 V140 M128 210 V140 M142 210 V140 M92 192 L150 156"/>
      <!-- tally group 3 -->
      <path d="M180 210 V100 M194 210 V100 M208 210 V100 M222 210 V100 M172 180 L230 128"/>
      <!-- tally group 4 -->
      <path d="M260 210 V50 M274 210 V50 M288 210 V50 M302 210 V50 M252 166 L310 90"/>
      <!-- growth line -->
      <path stroke="var(--ghost-soft)" stroke-width="4" d="M20 150 L110 118 L190 78 L300 20"/>
    </svg>
    <div class="back__brand">
      <span class="back__dot"></span>
      <span class="back__name">steered by tallies</span>
    </div>
  </section>

  <section class="card card--front" aria-label="Card front">
    <h1 class="front__name">steered by<br>tallies</h1>
    <svg class="front__chart" viewBox="0 0 230 220" aria-hidden="true"
         fill="none" stroke-width="9" stroke-linecap="round">
      <path stroke="var(--brand-red)" d="M20 200 H212"/>
      <path stroke="var(--brand-red)" d="M42 182 V140"/>
      <path stroke="var(--brand-peach)" d="M82 182 V112"/>
      <path stroke="var(--brand-orange)" d="M122 182 V84"/>
      <path stroke="var(--brand-peach)" d="M162 182 V56"/>
      <path stroke="var(--brand-red)" d="M202 182 V24"/>
      <path stroke="var(--brand-orange)" stroke-width="5" d="M30 110 L78 76 L118 52 L196 10"/>
    </svg>
    <div class="person">
      <p class="person__name">Dana Pellow</p>
      <p class="person__role">CEO / FOUNDER</p>
      <ul class="contacts">
        <li><svg viewBox="0 0 10 10"><path d="M2 0.5 L4 2.5 L3 3.8 Q4.2 6 6.2 7 L7.5 6 L9.5 8 L8 9.5 Q3 9 0.5 2 Z"/></svg><span>555 208 314</span></li>
        <li><svg viewBox="0 0 10 10"><path d="M0 2 H10 V8 H0 Z M0.8 2.6 L5 5.6 L9.2 2.6 V3.4 L5 6.4 L0.8 3.4 Z" fill-rule="evenodd"/></svg><span>dana@tallymail.com</span></li>
        <li><svg viewBox="0 0 10 10"><circle cx="5" cy="5" r="4.2" fill="none" stroke="var(--brand-red)" stroke-width="1.3"/></svg><span>www.<span class="accent">tallysteer</span>.com</span></li>
      </ul>
    </div>
  </section>

</main>
</body>
</html>
```